Business card design for my company.
I would like the card's background colour to be black. You can also see our web site to get an idea of our brand. https://www.tmwhomecrafting.com.au/
- Name
- Email

```html
<!DOCTYPE html>
<html lang="en">
<head>
<meta charset="utf-8">
<title>TMW Home Crafting – Business Card</title>
<link rel="stylesheet" href="https://fonts.googleapis.com/css2?family=Montserrat:wght@400;500;700&display=swap">
<style>
  :root {
    --stage: #e4e4e4;
    --card-black: #141414;
    --card-white: #ffffff;
    --brand-green: #1c9a3f;
    --ink: #1a1a1a;
    --logo-white: #f2f2f2;
  }
  * { box-sizing: border-box; margin: 0; padding: 0; }
  html, body {
    width: 1200px; height: 874px; overflow: hidden;
    background: var(--stage);
    font-family: "Montserrat", sans-serif;
  }
  .stage {
    width: 1200px; height: 874px;
    display: flex; flex-direction: column; align-items: center; justify-content: center;
    gap: 30px;
  }
  .card {
    position: relative;
    width: 630px; height: 360px;
    border-radius: 18px;
    overflow: hidden;
    box-shadow: 0 8px 24px rgba(0,0,0,.25);
  }
  /* Back */
  .card-back { background: var(--card-black); }
  .back-pattern {
    position: absolute; inset: 0;
    background: linear-gradient(125deg, #3a3a3a 0%, #1e1e1e 45%, #0d0d0d 100%);
  }
  /* Front */
  .card-front { background: var(--card-black); }
  .front-wave { position: absolute; inset: 0; width: 100%; height: 100%; }
  .brand-name {
    position: absolute; left: 46px; top: 70px;
    display: flex; align-items: center; gap: 14px;
    color: var(--logo-white);
    font-weight: 700; font-size: 34px; letter-spacing: 3px;
    text-transform: uppercase; line-height: 1.1;
  }
  .brand-square { width: 22px; height: 22px; background: var(--logo-white); flex: none; }
  .contact {
    position: absolute; right: 34px; top: 176px;
    text-align: right; color: var(--ink);
  }
  .contact-name { color: var(--brand-green); font-weight: 700; font-size: 27px; line-height: 1.1; }
  .contact-role { font-size: 15px; margin-top: 3px; }
  .contact-location { font-size: 15px; margin-top: 8px; }
  .contact-lines { list-style: none; margin-top: 10px; font-size: 15px; }
  .contact-lines li { display: flex; justify-content: flex-end; align-items: center; gap: 6px; line-height: 21px; }
  .contact-lines svg { width: 13px; height: 13px; fill: var(--brand-green); flex: none; }
</style>
</head>
<body>
<main class="stage">
  <section class="card card-back">
    <div class="back-pattern" role="img" aria-label="Repeating brand pattern in glossy black tones"></div>
  </section>

  <section class="card card-front">
    <svg class="front-wave" viewBox="0 0 630 360" preserveAspectRatio="none" aria-hidden="true">
      <path d="M0 250 C 120 330, 260 300, 360 220 C 440 160, 540 150, 630 150 L630 360 L0 360 Z" fill="var(--card-white)"/>
      <path d="M0 250 C 120 330, 260 300, 360 220 C 440 160, 540 150, 630 150" fill="none" stroke="var(--brand-green)" stroke-width="6"/>
    </svg>

    <div class="brand-name"><span class="brand-square"></span><span>TMW<br>Home Crafting</span></div>

    <div class="contact">
      <p class="contact-name">Liam Carver</p>
      <p class="contact-role">General Manager</p>
      <p class="contact-location">Bayside, Tasmania, Australia</p>
      <ul class="contact-lines">
        <li>0400 555 018
          <svg viewBox="0 0 24 24"><path d="M6.6 10.8a15 15 0 0 0 6.6 6.6l2.2-2.2c.3-.3.7-.4 1-.2 1.1.4 2.3.6 3.6.6.6 0 1 .4 1 1V20c0 .6-.4 1-1 1A17 17 0 0 1 3 4c0-.6.4-1 1-1h3.5c.6 0 1 .4 1 1 0 1.3.2 2.5.6 3.6.1.3 0 .7-.2 1z"/></svg></li>
        <li>info@tmwhomecrafting.com.au
          <svg viewBox="0 0 24 24"><path d="M2 5h20v14H2z M2 5l10 8 10-8" stroke="#fff" stroke-width="1.5"/></svg></li>
        <li>www.tmwhomecrafting.com.au
          <svg viewBox="0 0 24 24"><circle cx="12" cy="12" r="10"/></svg></li>
      </ul>
    </div>
  </section>
</main>
</body>
</html>
```